Website Redesign for Existing BBQ Catering Company

Need to get my website (HollowOakSmoke.com) redesigned. Looking for a cleaner look but still patriotic and rustic. Would like to add parallax scrolling on the menu page and include some pics from our photo gallery. Would like to display a picture of the brisket before scrolling into the meat section of our menu and the same for the other sections too.....picture of one of our sides, appetizers, desserts, etc.

Would also like to add three new pages called Corporate Events, Weddings, and Veteran Events possibly in a drop-down menu called Catering. You can use pics from our Facebook page. We've posted tons of pics from weddings that we've done. I've uploaded some corporate and wedding pics but you can pics the ones that look best. I can swap them out later if needed.

Would like to keep it Wordpress if possible so I can update it as needed.

Also need to add some links to our storefront on The Vow Loft. I have the HTML code and will upload the image here.

Also need to add social media links for our Facebook, Instagram and Twitter pages.

The contact form that I'm using now feeds the leads into another site called Tenbrim.com that I use to manage my clients.

Target Market(s)

Weddings, corporate events, veterans

Industry/Entity Type

Catering

Coding

Coded - Design and coding required

Number of Pages Required

5+ page

Colors
ec1f27
3176b5
ffffff

Requirements
Must have
• Really like the hero image design. Looks less like a template. Check out https://lumarenne.com and https://corvellagrille.com
• Would like to keep somewhat of a rustic and patriotic look and feel like the site currently is. We mainly cater in barn weddings and we cater for a lot of veterans. Will be pushing more corporate catering next year and opening a restaurant.

```html
<!DOCTYPE html>
<html lang="en">
<head>
<meta charset="utf-8">
<title>Hollow Oak Smoke BBQ Catering</title>
<link rel="stylesheet" href="https://fonts.googleapis.com/css2?family=Great+Vibes&family=Jost:wght@400;500&family=Lobster&family=Oswald:wght@400&display=swap">
<style>
:root{
  --red:#ec1f27;
  --blue:#3176b5;
  --white:#ffffff;
  --kraft:#d8bd93;
  --kraft-dark:#c9aa7c;
  --pattern:#eef0f3;
  --badge:#8ec1e6;
}
*{box-sizing:border-box;margin:0;padding:0}
html,body{width:862px;height:1200px;overflow:hidden}
body{
  position:relative;
  background:radial-gradient(ellipse at 50% 40%,#dcc39c 0%,var(--kraft) 60%,var(--kraft-dark) 100%);
  font-family:"Jost",sans-serif;
  color:var(--white);
}
.brand-seal{
  position:absolute;left:48px;top:22px;width:122px;height:122px;border-radius:50%;
  background:var(--blue);border:5px solid var(--white);
  box-shadow:0 0 0 3px var(--red),0 3px 8px rgba(0,0,0,.3);
  display:flex;align-items:center;justify-content:center;text-align:center;
  font-family:"Jost",sans-serif;font-weight:500;font-size:15px;line-height:1.15;color:var(--white);
  z-index:3;
}
.call-line{position:absolute;right:72px;top:20px;display:flex;align-items:baseline;gap:10px}
.call-line .call-label{font-family:"Lobster",cursive;font-size:25px;color:var(--red)}
.call-line .call-phone{font-family:"Oswald",sans-serif;font-size:25px;color:var(--white);text-shadow:0 1px 2px rgba(0,0,0,.35)}
.main-nav{
  position:absolute;right:72px;top:68px;display:flex;gap:27px;
  font-size:11.5px;font-weight:500;text-shadow:0 1px 2px rgba(0,0,0,.25)
}
.main-nav a{color:var(--white);text-decoration:none}
.main-nav a.current{color:var(--red);text-shadow:none}
.page{position:absolute;left:70px;top:102px;width:720px;box-shadow:0 4px 14px rgba(0,0,0,.25)}
.hero{
  position:relative;height:346px;overflow:hidden;
  background:
    radial-gradient(ellipse at 80% 15%,rgba(40,35,40,.85) 0%,transparent 45%),
    linear-gradient(160deg,#6b4a3e 0%,#8a3a2c 30%,#5a2a20 50%,#9c4a3a 65%,#3e2620 85%,#6e5048 100%);
}
.hero-title{
  position:absolute;left:0;right:0;top:146px;transform:translateY(-50%);
  text-align:center;font-family:"Great Vibes",cursive;font-size:58px;line-height:1;color:var(--white);
  text-shadow:0 2px 6px rgba(0,0,0,.5);
}
.slider-dots{position:absolute;left:0;right:0;top:303px;display:flex;justify-content:center;gap:3px}
.slider-dots span{width:12px;height:12px;border-radius:50%;background:var(--white)}
.slider-dots span.active{background:transparent;border:2px solid var(--white)}
.welcome{background:var(--blue);height:254px;text-align:center;padding-top:36px}
.welcome h1{font-family:"Great Vibes",cursive;font-weight:400;font-size:40px;line-height:48px;margin-bottom:10px}
.welcome p{font-size:9.6px;line-height:19px;width:630px;margin:0 auto 16px}
.features{
  position:relative;height:348px;background-color:var(--white);
  background-image:radial-gradient(circle,var(--pattern) 1.5px,transparent 2px);
  background-size:12px 12px;
}
.card{position:absolute;top:34px;width:190px}
.card .card-photo{display:block;width:190px;height:132px}
.card-body{position:relative;background:var(--blue);height:128px;text-align:center;padding-top:10px;box-shadow:0 2px 5px rgba(0,0,0,.2)}
.card-body h2{font-family:"Great Vibes",cursive;font-weight:400;font-size:28px;line-height:30px;margin-bottom:6px}
.card-body p{font-size:8px;line-height:12px;width:172px;margin:0 auto}
.read-more{position:absolute;left:50%;top:91px;transform:translateX(-50%);background:var(--red);color:var(--white);font-size:7.6px;line-height:14px;padding:0 13px;border-radius:8px;text-decoration:none;white-space:nowrap}
.card-about{left:32px}.card-menu{left:266px}.card-contact{left:500px}
.footer{position:relative;height:94px;background:var(--red)}
.footer-edge{position:absolute;left:0;top:-6px;width:720px;height:7px;display:block}
.listing-badge{position:absolute;left:326px;top:-41px;width:70px;height:70px;border-radius:50%;background:var(--badge);border:3px solid var(--white);box-shadow:0 0 0 1px var(--badge)}
.footer-nav{position:absolute;top:34px;left:0;right:0;display:flex;justify-content:center;font-size:7.5px}
.footer-nav a{color:#f6b9bb;text-decoration:none;padding:0 9px;border-left:1px solid #f08c90}
.footer-nav a:first-child{border-left:none}
.copyright{position:absolute;left:24px;top:64px;font-size:9.5px}
.social{position:absolute;right:22px;top:66px;display:flex;gap:6px}
.social span{width:8px;height:8px;border-radius:50%;background:var(--white)}
</style>
</head>
<body>
<div class="brand-seal">Hollow<br>Oak<br>Smoke</div>

<div class="call-line"><span class="call-label">Call Us Today ! ! !</span><span class="call-phone">012-555-0148</span></div>
<nav class="main-nav">
  <a class="current" href="#">Home</a><a href="#">Menu</a><a href="#">Photo Gallery</a><a href="#">Corporate Catering</a><a href="#">Weddings</a><a href="#">Veteran Events</a><a href="#">Contact</a>
</nav>

<main class="page">
  <section class="hero" role="img" aria-label="Photo of sliced smoked brisket being cut with a knife">
    <div class="hero-title">Hollow Oak Smoke</div>
    <div class="slider-dots"><span class="active"></span><span></span><span></span><span></span></div>
  </section>

  <section class="welcome">
    <h1>Welcome to Hollow Oak Smoke</h1>
    <p>Sed ut perspiciatis unde omnis iste natus error sit voluptatem accusantium doloremque laudantium, totam rem aperiam, eaque ipsa quae ab illo inventore veritatis et quasi architecto beatae vitae dicta sunt explicabo. Nemo enim ipsam voluptatem quia voluptas sit aspernatur aut odit aut fugit, sed quia consequuntur magni dolores eos qui ratione voluptatem sequi nesciunt.</p>
    <p>But I must explain to you how all this mistaken idea of denouncing pleasure and praising pain was born and I will give you a complete account of the system, and expound the actual teachings of the great explorer of the truth, the master-builder of human happiness.</p>
  </section>

  <section class="features">
    <article class="card card-about">
      <svg class="card-photo" viewBox="0 0 190 132" role="img" aria-label="Photo of the catering team serving food at an outdoor event">
        <defs><linearGradient id="g-about" x1="0" y1="0" x2="0" y2="1"><stop offset="0" stop-color="#9fb6c9"/><stop offset=".5" stop-color="#a8586a"/><stop offset="1" stop-color="#2a2a2e"/></linearGradient></defs>
        <path d="M1,132 V40 Q1,22 16,22 Q22,4 44,8 Q60,0 76,6 Q95,-2 114,6 Q130,0 146,8 Q168,4 174,22 Q189,22 189,40 V132 Z" fill="url(#g-about)" stroke="#3176b5" stroke-width="2"/>
      </svg>
      <div class="card-body">
        <h2>About Us</h2>
        <p>Hollow Oak Smoke is a BBQ Catering Company opened with a mission to give back to the veteran community.</p>
        <a class="read-more" href="#">Read more</a>
      </div>
    </article>
    <article class="card card-menu">
      <svg class="card-photo" viewBox="0 0 190 132" role="img" aria-label="Photo of a berry pie with a flag-style lattice crust">
        <defs><linearGradient id="g-menu" x1="0" y1="0" x2="0" y2="1"><stop offset="0" stop-color="#c9a884"/><stop offset=".5" stop-color="#4a3346"/><stop offset="1" stop-color="#d8b48e"/></linearGradient></defs>
        <path d="M1,132 V40 Q1,22 16,22 Q22,4 44,8 Q60,0 76,6 Q95,-2 114,6 Q130,0 146,8 Q168,4 174,22 Q189,22 189,40 V132 Z" fill="url(#g-menu)" stroke="#3176b5" stroke-width="2"/>
      </svg>
      <div class="card-body">
        <h2>Our Menu</h2>
        <p>Hollow Oak Smoke is committed to serving amazing BBQ. We don't take shortcuts and put a lot of love into our BBQ that we guarantee..</p>
        <a class="read-more" href="#">Read more</a>
      </div>
    </article>
    <article class="card card-contact">
      <svg class="card-photo" viewBox="0 0 190 132" role="img" aria-label="Photo of a smoker trailer parked outside the shop">
        <defs><linearGradient id="g-contact" x1="0" y1="0" x2="0" y2="1"><stop offset="0" stop-color="#7fb0dc"/><stop offset=".45" stop-color="#d9d4cc"/><stop offset=".75" stop-color="#3a3a3c"/><stop offset="1" stop-color="#8c8a86"/></linearGradient></defs>
        <path d="M1,132 V40 Q1,22 16,22 Q22,4 44,8 Q60,0 76,6 Q95,-2 114,6 Q130,0 146,8 Q168,4 174,22 Q189,22 189,40 V132 Z" fill="url(#g-contact)" stroke="#3176b5" stroke-width="2"/>
      </svg>
      <div class="card-body">
        <h2>Contact Us</h2>
        <p>Feel free to contact us with any questions you might have. We'd love to hear from ya.</p>
        <a class="read-more" href="#">Read more</a>
      </div>
    </article>
  </section>

  <footer class="footer">
    <svg class="footer-edge" viewBox="0 0 720 7" preserveAspectRatio="none">
      <defs>
        <pattern id="zigzag" width="6" height="7" patternUnits="userSpaceOnUse">
          <path d="M0,7 L0,3 L3,0 L6,3 L6,7 Z" fill="#ec1f27"/>
        </pattern>
      </defs>
      <rect x="0" y="0" width="720" height="7" fill="url(#zigzag)"/>
    </svg>
    <div class="listing-badge" role="img" aria-label="The Vow Loft listing badge"></div>
    <nav class="footer-nav">
      <a href="#">Home</a><a href="#">Menu</a><a href="#">Photo Gallery</a><a href="#">Corporate Catering</a><a href="#">Weddings</a><a href="#">Veteran Events</a><a href="#">Contact</a>
    </nav>
    <p class="copyright">Copyright 2017 © Hollow Oak Smoke. All rights reserved.</p>
    <div class="social" aria-label="Social media links"><span></span><span></span><span></span></div>
  </footer>
</main>
</body>
</html>
```